Walk Beside The River

Business Card design

Target Market(s)

People who require support in the commnity

Industry/Entity Type

Mental Health Support

Contact Information for Business Card

Mental Health Support Rosalind Tavener walkbesidetheriver@mailcove.com.au 0481 637 092 PO Box 926 Fernhollow Bay 7093

Colors
6B429C
8869AF
B7A5CE
E3DAEB
F3F0F8

Requirements
Must have
• Logo & details listed above
Should not have
• No red or orange

```html
<!DOCTYPE html>
<html lang="en">
<head>
<meta charset="utf-8">
<title>Walk Beside The River – Business Card</title>
<link href="https://fonts.googleapis.com/css2?family=Montserrat:wght@500;700;800&display=swap" rel="stylesheet">
<style>
  :root {
    --purple: #6B429C;
    --purple-mid: #8869AF;
    --lavender: #E3DAEB;
    --sun: #F4E82A;
    --ink: #1d1a22;
    --paper: #ffffff;
    --backdrop: #ece9f0;
  }
  * { box-sizing: border-box; margin: 0; padding: 0; }
  html, body { width: 1200px; height: 900px; overflow: hidden; }
  body {
    background: var(--backdrop);
    font-family: "Montserrat", sans-serif;
    position: relative;
  }
  .card {
    position: absolute;
    width: 600px;
    height: 343px;
    background: var(--paper);
    box-shadow: 0 10px 28px rgba(40, 30, 60, 0.22);
    overflow: hidden;
  }
  .card--front { left: 70px; top: 80px; }
  .card--back { left: 530px; top: 477px; }

  .brand {
    display: flex;
    align-items: center;
    justify-content: center;
    gap: 14px;
  }
  .brand__dot {
    border-radius: 50%;
    background: var(--purple);
    flex: none;
  }
  .brand__name {
    color: var(--purple);
    font-weight: 800;
    letter-spacing: 0.08em;
    text-transform: uppercase;
    line-height: 1.15;
  }
  .card--front .brand {
    position: absolute;
    inset: 0;
  }
  .card--front .brand__dot { width: 64px; height: 64px; }
  .card--front .brand__name { font-size: 26px; }

  .card--back .brand {
    position: absolute;
    left: 0; right: 0; top: 52px;
  }
  .card--back .brand__dot { width: 40px; height: 40px; }
  .card--back .brand__name { font-size: 17px; }

  .wave {
    position: absolute;
    left: 0; top: 0;
    width: 600px; height: 343px;
  }
  .details {
    position: absolute;
    left: 54px;
    top: 140px;
    color: var(--ink);
    font-weight: 500;
    font-size: 15px;
  }
  .details__title {
    color: var(--purple);
    font-weight: 800;
    font-size: 16px;
    letter-spacing: 0.01em;
    text-transform: uppercase;
    margin-bottom: 8px;
  }
  .details__line {
    display: flex;
    align-items: center;
    gap: 7px;
    margin-bottom: 7px;
    white-space: nowrap;
  }
  .details__line--address { padding-left: 36px; }
  .icon { width: 16px; height: 16px; fill: var(--purple); flex: none; }
  .gap { width: 8px; }
</style>
</head>
<body>

<section class="card card--front">
  <div class="brand">
    <span class="brand__dot"></span>
    <span class="brand__name">Walk Beside<br>The River</span>
  </div>
</section>

<section class="card card--back">
  <svg class="wave" viewBox="0 0 600 343" aria-hidden="true">
    <path fill="var(--sun)" d="M160,300 C260,294 350,282 440,256 C500,238 545,226 585,220 C545,230 500,244 445,264 C355,294 260,306 160,300 Z"/>
    <path fill="var(--purple)" d="M0,314 C140,308 260,300 360,282 C460,262 530,244 600,236 L600,343 L0,343 Z"/>
  </svg>

  <div class="brand">
    <span class="brand__dot"></span>
    <span class="brand__name">Walk Beside The River</span>
  </div>

  <div class="details">
    <p class="details__title">Mental Health Support Rosalind Tavener</p>
    <p class="details__line details__line--address">
      <svg class="icon" viewBox="0 0 24 24" aria-hidden="true"><path d="M12 2a7 7 0 0 0-7 7c0 5.2 7 13 7 13s7-7.8 7-13a7 7 0 0 0-7-7zm0 9.5A2.5 2.5 0 1 1 12 6.5a2.5 2.5 0 0 1 0 5z"/></svg>
      PO Box 926 Fernhollow Bay 7093
    </p>
    <p class="details__line">
      <svg class="icon" viewBox="0 0 24 24" aria-hidden="true"><path d="M3 9c0-3 4-5 9-5s9 2 9 5v2h-5V9H8v2H3zM6 12h12l2 7H4z"/></svg>
      0481 637 092
      <span class="gap"></span>
      <svg class="icon" viewBox="0 0 24 24" aria-hidden="true"><path d="M2 5h20v14H2zm2 2v.5l8 5.5 8-5.5V7z"/></svg>
      walkbesidetheriver@mailcove.com.au
    </p>
  </div>
</section>

</body>
</html>
```